business card

Business card for new business.
Red and black corporate colors.
Card can have an Indsutrial feel to it. Feel free to add Rust, Bolted steel, or graphics as you see fit. We provide highly specialized services to the below mentioned industries.
Keep information out of corners so that if I want I can choose rounded corners.
Information
- front. name - title - phone - email
- Rear
Welding - Piping - Fabrication - Rigging - Power
Redmarsh - Ashford Bay - Port Kellan - Stonebridge - Halvern

```html
<!DOCTYPE html>
<html lang="en">
<head>
<meta charset="utf-8">
<title>Ironspan business card</title>
<link href="https://fonts.googleapis.com/css2?family=Roboto:wght@300;400;500;900&display=swap" rel="stylesheet">
<style>
  :root {
    --bg: #242424;
    --red: #ed1c24;
    --red-soft: #f2454b;
    --white: #ffffff;
  }
  html, body {
    margin: 0;
    width: 1200px;
    height: 930px;
    overflow: hidden;
    background: var(--bg);
    font-family: "Roboto", sans-serif;
  }
  .canvas { position: relative; width: 1200px; height: 930px; }
  .card {
    position: absolute;
    width: 580px;
    height: 330px;
    border-radius: 16px;
    background: var(--red);
    color: var(--white);
    overflow: hidden;
    box-shadow: 0 14px 30px rgba(0,0,0,.45);
  }
  /* rear card */
  .card-rear { left: 90px; top: 110px; }
  .card-rear .wordmark {
    position: absolute;
    left: 0; right: 0; top: 100px;
    text-align: center;
    font-weight: 900;
    font-size: 62px;
    letter-spacing: 1px;
  }
  .card-rear .lines {
    position: absolute;
    left: 0; right: 0; bottom: 44px;
    text-align: center;
    font-weight: 300;
    font-size: 14px;
    line-height: 21px;
  }
  .card-rear .lines p { margin: 0; }
  /* front card */
  .card-front { left: 530px; top: 480px; }
  .brand-strip {
    position: absolute;
    left: 0; top: 0; bottom: 0;
    width: 130px;
    background: var(--white);
  }
  .brand-strip .wordmark {
    position: absolute;
    left: 65px; top: 165px;
    transform: translate(-50%, -50%) rotate(-90deg);
    font-weight: 900;
    font-size: 48px;
    color: var(--red);
    white-space: nowrap;
  }
  .map-area {
    position: absolute;
    left: 290px; top: 30px;
    width: 270px; height: 170px;
    border-radius: 40px;
    background: radial-gradient(ellipse at center, var(--red-soft) 0%, var(--red) 75%);
  }
  .details { position: absolute; left: 160px; top: 34px; }
  .person-name { margin: 0; font-size: 22px; font-weight: 500; letter-spacing: .5px; }
  .person-title { margin: 2px 0 0; font-size: 14px; font-weight: 300; }
  .rule { width: 14px; height: 1px; background: var(--white); margin: 26px 0 16px; }
  .address { margin: 0; font-size: 14px; line-height: 20px; font-weight: 400; }
  .contacts { list-style: none; margin: 0; padding: 0; font-size: 14px; line-height: 22px; }
  .contacts li { display: flex; align-items: center; gap: 8px; }
  .contacts svg { width: 11px; height: 11px; fill: none; stroke: var(--white); stroke-width: 1.6; }
</style>
</head>
<body>
<div class="canvas">
  <section class="card card-rear">
    <div class="wordmark">IRONSPAN</div>
    <div class="lines">
      <p>Welding - Piping - Fabrication - Rigging - Power</p>
      <p>Redmarsh - Ashford Bay - Port Kellan - Stonebridge - Halvern</p>
    </div>
  </section>

  <section class="card card-front">
    <div class="brand-strip"><div class="wordmark">IRONSPAN</div></div>
    <div class="map-area" role="img" aria-label="Dotted world map in light red"></div>
    <div class="details">
      <h1 class="person-name">DANIEL HARPER</h1>
      <p class="person-title">Director</p>
      <div class="rule"></div>
      <p class="address">2750 Granite Way<br>Dunmore, NV 89417</p>
      <div class="rule"></div>
      <ul class="contacts">
        <li><svg viewBox="0 0 12 12"><path d="M2 1h3l1 3-2 1c1 2 2 3 4 4l1-2 3 1v3c-6 0-10-4-10-10z"/></svg>+555 5512-0467</li>
        <li><svg viewBox="0 0 12 12"><rect x="1" y="2.5" width="10" height="7"/><path d="M1 2.5l5 4 5-4"/></svg>info@ironspan.com</li>
        <li><svg viewBox="0 0 12 12"><circle cx="6" cy="6" r="5"/><path d="M1 6h10M6 1c-3 3-3 7 0 10M6 1c3 3 3 7 0 10"/></svg>www.ironspan.com</li>
      </ul>
    </div>
  </section>
</div>
</body>
</html>
```